Orbit Voltix VR is the name of our project, We are a Virtual Reality Theme park

We need a web page and logo that is sharp and exciting, and futuristic that people would want to have on a tee shirt.. We like teal -black- silver colour. Customers will be able to book on line- we will have Free Roam VR experiences , Trundla(treadmills), Stand alone VR stations and VR Simulator rides.

Orbit Voltix VR

```html
<!DOCTYPE html>
<html lang="en">
<head>
<meta charset="utf-8">
<title>Orbit Voltix VR</title>
<link href="https://fonts.googleapis.com/css2?family=Lato:wght@400;700;900&display=swap" rel="stylesheet">
<style>
:root{
  --teal:#1fc3a0;
  --teal-dark:#17a98a;
  --ink:#111111;
  --text:#333333;
  --muted:#555555;
  --light-bg:#efefef;
  --white:#ffffff;
  --dark:#232425;
}
*{box-sizing:border-box;margin:0;padding:0}
html,body{width:1200px;height:3468px;overflow:hidden}
body{font-family:'Lato',sans-serif;color:var(--text);background:var(--white);position:relative}
.abs{position:absolute}
.btn{position:absolute;background:var(--teal);color:var(--white);font-weight:700;font-size:20px;display:flex;align-items:center;justify-content:center}

/* hero */
.hero{left:0;top:0;width:1200px;height:664px;background:linear-gradient(160deg,#8a939a 0%,#6c7479 45%,#4f5459 75%,#7a6f54 100%)}
.brand{left:76px;top:58px;font-size:30px;font-weight:700;color:var(--white);line-height:40px}
.nav{right:76px;top:58px;display:flex;gap:6px}
.nav a{color:var(--white);font-size:18px;font-weight:700;text-decoration:none;height:39px;padding:0 14px;display:flex;align-items:center}
.nav a.active{background:var(--teal);padding:0 24px}
.hero-title{left:0;width:1200px;top:275px;text-align:center;color:var(--white);font-weight:700;font-size:70px;line-height:80px}
.hero-sub{left:0;width:1200px;top:352px;text-align:center;color:var(--white);font-weight:700;font-size:44px;line-height:54px}
.dots{left:566px;top:614px;display:flex;gap:8px}
.dots span{width:11px;height:11px;border-radius:50%;background:var(--white)}
.dots span:first-child{background:var(--teal)}

/* welcome */
.section-title{left:0;width:1200px;text-align:center;color:var(--ink);font-weight:700;font-size:44px;line-height:54px}
.welcome-text{left:160px;width:880px;top:788px;text-align:center;font-size:16px;line-height:30px;color:var(--muted)}

/* what we do */
.what{left:0;top:1068px;width:1200px;height:546px;background:var(--light-bg)}
.what-title{left:94px;top:1110px;font-size:44px;font-weight:700;color:var(--ink);line-height:54px}
.what-text{left:80px;width:330px;top:1182px;text-align:center;font-size:16px;line-height:29px;color:var(--muted)}
.tile{position:absolute;display:flex;align-items:flex-end;padding:0 0 14px 20px;color:var(--white);font-weight:700;font-size:26px;line-height:30px}

/* testimonial */
.testimonial{left:0;top:1614px;width:1200px;height:437px;background:linear-gradient(90deg,#2a2b2c,#3a3b3c 55%,#1e1f20)}
.quote-text{left:165px;width:870px;top:1735px;text-align:center;color:#dddddd;font-size:16px;line-height:30px}
.quote-mark{color:var(--teal);font-size:60px;font-weight:900;line-height:60px}
.quote-name{left:0;width:1200px;top:1834px;text-align:center;color:var(--teal);font-size:20px;font-weight:700}
.avatar{left:547px;top:1876px;width:104px;height:104px;border-radius:50%;border:4px solid var(--white);background:#8c7a6a}

/* gallery */
.photo{position:absolute}

/* blog */
.blog-bg{left:587px;top:2751px;width:613px;height:426px;background:var(--light-bg)}
.blog-image{left:0;top:2751px;width:587px;height:426px;background:linear-gradient(135deg,#2e3436,#1b1e20 60%,#3b4a55)}
.blog-title{left:0;width:455px;top:2826px;text-align:center;color:var(--white);font-size:40px;font-weight:700}
.blog-text{left:80px;width:300px;top:2892px;text-align:center;color:#e6e6e6;font-size:16px;line-height:30px}
.blog-card{left:407px;top:2828px;width:719px;height:275px;background:var(--teal);padding:26px 28px;color:var(--white)}
.blog-card h3{font-size:31px;line-height:36px;font-weight:700;margin-bottom:14px}
.blog-card p{font-size:14px;line-height:25px}
.blog-card .date{font-weight:700;font-size:16px;margin-top:22px}

/* footer */
.foot-brand{left:76px;top:3257px;font-size:26px;font-weight:700;color:var(--ink)}
.foot-copy{left:76px;top:3302px;font-size:13px;line-height:22px;color:var(--text)}
.follow{left:76px;top:3362px;font-size:19px;font-weight:700;color:var(--teal)}
.social{left:76px;top:3405px;display:flex;gap:18px}
.social span{width:20px;height:20px;border-radius:50%;background:#222}
.foot-head{font-size:21px;font-weight:700;color:var(--ink)}
.foot-list{font-size:15px;line-height:31px;color:var(--text);list-style:none}
.email{left:883px;top:3274px;width:243px;height:39px;background:#e5e5e5;font-size:12px;color:#333;padding-left:14px;display:flex;align-items:center}
</style>
</head>
<body>

<header class="abs hero" role="img" aria-label="Photo of a woman wearing a VR headset riding a yellow roller coaster track"></header>
<div class="abs brand">Orbit Voltix VR</div>
<nav class="abs nav">
  <a class="active">Home</a><a>About Us</a><a>Services</a><a>Gallery</a><a>Blog</a><a>Contact Us</a>
</nav>
<h1 class="abs hero-title">Orbit Voltix VR</h1>
<p class="abs hero-sub">We are a Virtual Reality Theme park.</p>
<div class="abs dots"><span></span><span></span><span></span><span></span></div>

<h2 class="abs section-title" style="top:716px">Welcome to Our Website</h2>
<p class="abs welcome-text">Lorem ipsum dolor sit amet, consectetur adipiscing elit. Morbi et nibh velit. Ut sem metus, mollis eget faucibus eu, pretium sit amet quam. In sem turpis, ornare vel est nec, lacinia lacinia sapien. Duis viverra feugiat lectus, vitae ultricies massa ultricies imperdiet. Pellentesque eget justo mi. Nunc sollicitudin rutrum ipsum quis accumsan. Sed in lobortis arcu. Integer non sodales leo.</p>
<div class="btn" style="left:511px;top:955px;width:178px;height:53px">Read More</div>

<section class="abs what"></section>
<h2 class="abs what-title">What We Do</h2>
<p class="abs what-text">Lorem ipsum dolor sit amet, consectetur adipiscing elit. Morbi et nibh velit. Ut sem metus, mollis eget faucibus eu, pretium sit amet quam. In sem turpis, ornare vel est nec, lacinia lacinia sapien. viverra feugiat lectus, vitae ultricies massa ultricies imperdiet. Pellentesque eget justo mi. Nunc sollicitudin rutrum ipsum quis accumsan. Sed in lobortis arcu. Integer non sodales leo.</p>
<div class="btn" style="left:127px;top:1514px;width:180px;height:51px">Read More</div>

<div class="tile" style="left:435px;top:1121px;width:386px;height:215px;background:linear-gradient(135deg,#7e8c96,#3d5a78 60%,#c9a640)" role="img" aria-label="Person in VR headset mid free roam experience">Free Roam<br>VR Experiences</div>
<div class="tile" style="left:832px;top:1121px;width:294px;height:215px;background:linear-gradient(135deg,#3a4450,#1d2128 60%,#5a6a80)" role="img" aria-label="VR treadmill rigs in an arcade">Trundla<br>(Treadmills)</div>
<div class="tile" style="left:435px;top:1348px;width:291px;height:215px;background:linear-gradient(135deg,#2c3a52,#4d5d7a 50%,#1b2230)" role="img" aria-label="Row of egg shaped VR chairs">Stand Alone VR<br>Stations</div>
<div class="tile" style="left:740px;top:1348px;width:386px;height:215px;background:linear-gradient(135deg,#3b1f55,#5a2d7a 55%,#1f1230)" role="img" aria-label="Rider on a VR simulator under purple light">VR Simulator<br>Rides</div>

<section class="abs testimonial" role="img" aria-label="Dim photo of a person wearing a VR headset"></section>
<h2 class="abs section-title" style="top:1662px;color:var(--white)">What Our User Says</h2>
<div class="abs quote-mark" style="left:108px;top:1730px">&ldquo;</div>
<div class="abs quote-mark" style="left:1060px;top:1730px">&rdquo;</div>
<p class="abs quote-text">Lorem ipsum dolor sit amet, consectetur adipiscing elit. Morbi et nibh velit. Ut sem metus, mollis eget faucibus eu, pretium sit amet quam. In sem turpis, ornare vel est nec, lacinia lacinia sapien. Duis viverra feugiat lectus, vitae ultricies massa ultricies imperdiet...</p>
<div class="abs quote-name">-Name Heading</div>
<div class="abs avatar" role="img" aria-label="Customer portrait"></div>

<h2 class="abs section-title" style="top:2105px">Gallery</h2>
<div class="photo" style="left:76px;top:2196px;width:340px;height:234px;background:linear-gradient(135deg,#dfe6ee,#3b5fa0 55%,#1c2230)" role="img" aria-label="Egg shaped VR chair in an arcade"></div>
<div class="photo" style="left:430px;top:2196px;width:342px;height:234px;background:linear-gradient(160deg,#a9c2d6,#6b8f6a 45%,#c98a3a)" role="img" aria-label="Riders on an outdoor roller coaster"></div>
<div class="photo" style="left:786px;top:2196px;width:340px;height:234px;background:linear-gradient(135deg,#4a5a70,#2c3440 50%,#3c58a0)" role="img" aria-label="Man in VR headset on a motorbike simulator"></div>
<div class="photo" style="left:76px;top:2448px;width:516px;height:234px;background:linear-gradient(135deg,#e4e8ea,#b8c2c6 50%,#6a5a48)" role="img" aria-label="Friends cheering in VR headsets"></div>
<div class="photo" style="left:606px;top:2448px;width:520px;height:234px;background:linear-gradient(160deg,#9aa4ab,#6d767c 50%,#c2a24a)" role="img" aria-label="Woman in VR headset on a roller coaster"></div>

<section class="abs blog-bg"></section>
<div class="abs blog-image" role="img" aria-label="Dark photo of VR chairs"></div>
<h2 class="abs blog-title">Blog Post</h2>
<p class="abs blog-text">Lorem ipsum dolor sit amet, consectetur adipiscing elit. Morbi et nibh velit. Ut sem metus, mollis eget faucibus eu, pretium sit amet quam.</p>
<div class="btn" style="left:141px;top:3043px;width:178px;height:53px">Read More</div>
<article class="abs blog-card">
  <h3>Class aptent taciti sociosqu ad litora torquent per conubia nostra...</h3>
  <p>Aenean quis neque venenatis urna gravida ultrices. Cras viverra tempor libero varius natoque penatibus et magnis dis parturient montes, nascetur ridiculus mus. Maecenas faucibus pellentesque orci quis ullamcorper. Suspendisse magna eros, varius ac nibh ac, ullamcorper tincidunt dui.</p>
  <p class="date">March 10, 2019</p>
</article>

<footer>
  <div class="abs foot-brand">Orbit Voltix VR</div>
  <div class="abs foot-copy">Copyright © 2019 Company Name<br>All Right reserved</div>
  <div class="abs follow">Follow Us</div>
  <div class="abs social" aria-label="Social links"><span></span><span></span><span></span><span></span><span></span></div>

  <div class="abs foot-head" style="left:370px;top:3228px">Site Map</div>
  <ul class="abs foot-list" style="left:370px;top:3261px"><li>Home</li><li>About Us</li><li>Services</li><li>Gallery</li></ul>
  <ul class="abs foot-list" style="left:485px;top:3261px"><li>Blog</li><li>Contact Us</li></ul>

  <div class="abs foot-head" style="left:633px;top:3228px">Services</div>
  <ul class="abs foot-list" style="left:633px;top:3261px"><li>Free Roam VR experiences</li><li>Trundla(treadmills)</li><li>Stand alone VR stations</li><li>VR Simulator rides</li></ul>

  <div class="abs foot-head" style="left:883px;top:3228px">Email Sign Up</div>
  <div class="abs email">Enter Email Address</div>
  <div class="btn" style="left:1017px;top:3325px;width:109px;height:35px;font-size:17px">Sign Up</div>
</footer>

</body>
</html>
```